Super elegant, crisp & clean Business card design required

We recently upgraded our branding - which is on our website - talvendoraphoto.com

I would like a simple, yet elegant, clean business card design please.

The font of my logo is Cinzel - and because of the natural colour - it's best to have this on a black background.

I would like to have the back of the business card - with simply my logo.

PLEASE DO NOT SUBMIT A COMPLICATED / UNCLEAN DESIGN

Industry/Entity Type

Business

Contact Information for Business Card

Talven Doroshko Photography

Font styles to use
Other font styles liked:
• Cinzel

Requirements
Must have
• A backpage with nothing but my logo
• Simple design - stands out
Should not have
• Colour that dont align with my logo
• Over complicated '/ non symmetrical design

```html
<!DOCTYPE html>
<html lang="en">
<head>
<meta charset="utf-8">
<title>Talven Doroshko Photography — Business Cards</title>
<link href="https://fonts.googleapis.com/css2?family=Cinzel:wght@400&family=Questrial&display=swap" rel="stylesheet">
<style>
  :root {
    --backdrop: #2a2a2b;
    --card-black: #0d0d0e;
    --silver: #bdbdbf;
    --gold: #b08a5a;
    --gold-soft: rgba(176, 138, 90, 0.75);
  }
  * { margin: 0; padding: 0; box-sizing: border-box; }
  html, body {
    width: 1200px;
    height: 767px;
    overflow: hidden;
    background: var(--backdrop);
  }
  .canvas {
    position: relative;
    width: 1200px;
    height: 767px;
    display: flex;
    align-items: center;
    justify-content: center;
    gap: 60px;
  }
  .card {
    width: 500px;
    height: 286px;
    background: var(--card-black);
    border-radius: 3px;
    display: flex;
    flex-direction: column;
    align-items: center;
    justify-content: center;
    text-align: center;
  }
  .brand-name {
    font-family: "Cinzel", serif;
    font-weight: 400;
    line-height: 1.15;
  }
  .brand-name .brand-main {
    display: block;
    font-size: 22px;
    letter-spacing: 0.04em;
  }
  .brand-name .brand-sub {
    display: block;
    font-size: 12px;
    letter-spacing: 0.55em;
    padding-left: 0.55em;
  }
  .card--back .brand-name { color: var(--silver); }
  .card--front .brand-name { color: var(--gold); margin-top: -10px; }
  .divider {
    width: 300px;
    height: 1px;
    margin: 16px 0 14px;
    background: linear-gradient(90deg, transparent, var(--gold) 20%, var(--gold) 80%, transparent);
  }
  .contact {
    font-family: "Questrial", sans-serif;
    font-size: 13px;
    line-height: 1.55;
    color: var(--gold-soft);
    letter-spacing: 0.02em;
  }
  .contact .label { color: var(--gold); }
</style>
</head>
<body>
  <main class="canvas">
    <section class="card card--back" aria-label="Card back">
      <h1 class="brand-name">
        <span class="brand-main">Talven Doroshko</span>
        <span class="brand-sub">Photography</span>
      </h1>
    </section>

    <section class="card card--front" aria-label="Card front">
      <h2 class="brand-name">
        <span class="brand-main">Talven Doroshko</span>
        <span class="brand-sub">Photography</span>
      </h2>
      <div class="divider"></div>
      <address class="contact" style="font-style: normal;">
        <div><span class="label">T:</span> 07700900123 · <span class="label">E:</span> info@talvendoraphoto.com</div>
        <div>www.talvendoraphoto.com</div>
      </address>
    </section>
  </main>
</body>
</html>
```